New Business Card for Web Design/Internet Marketing Company

Looking for a great looking new business card. We are a 10 year old web design, internet marketing and website management company that works mostly with small businesses.

Our new card needs to better match the colors and style of our website, be bold, extremely usable and slightly edgy.

Target Market(s)

Small/Medium businesses that have websites

Industry/Entity Type

Internet

Requirements
Must have
• Front and back design, full color, rounded corners please

Must use the colors/style of our website (JPG provided)

INFO FOR CARDS (as readable as possible please)
Mark Lenner
President/CEO
mark@trelvanmedia.example
Phone: 520-381-7459
Toll Free: 866-381-7459
Address: 4315 W. Calloway Ave. Ste. 140, Tucson, AZ 85792

THINGS I WANT TO PROMOTE (if there is room):
1. Our Website - www.trelvanmedia.example

2. Social Media
Twitter: @trelvanmedia
Facebook: www.facebook.com/trelvanmedia

3. Our Services
Web Design
Internet Marketing
Website Management

```html
<!DOCTYPE html>
<html lang="en">
<head>
<meta charset="utf-8">
<title>Trelvan Media – Business Cards</title>
<link rel="stylesheet" href="https://fonts.googleapis.com/css2?family=Open+Sans:wght@400;600;700&display=swap">
<style>
  :root {
    --bg: #e9e9ea;
    --card: #ffffff;
    --blue: #1a86c7;
    --navy: #2b3f8f;
    --orange: #f07d1e;
    --ink: #3f3f3f;
    --muted: #555a60;
  }
  * { box-sizing: border-box; margin: 0; padding: 0; }
  html, body { width: 1200px; height: 944px; overflow: hidden; }
  body {
    background: var(--bg);
    font-family: "Open Sans", Arial, sans-serif;
    color: var(--ink);
    position: relative;
  }
  .card {
    position: absolute;
    width: 540px;
    height: 310px;
    background: var(--card);
    border-radius: 20px;
    overflow: hidden;
    box-shadow: 0 6px 18px rgba(0,0,0,0.18);
  }
  .card--front { left: 40px; top: 317px; }
  .card--back  { left: 620px; top: 317px; }

  .brand {
    position: absolute;
    display: flex;
    align-items: center;
    gap: 12px;
  }
  .brand__dot {
    width: 40px; height: 40px;
    border-radius: 50%;
    background: var(--orange);
  }
  .brand__name {
    font-weight: 700;
    font-size: 40px;
    color: var(--blue);
    letter-spacing: -0.5px;
    line-height: 1;
  }
  .card--front .brand { left: 70px; top: 62px; }
  .card--back .brand  { left: 90px; top: 40px; }

  .services {
    position: absolute;
    left: 0; right: 0;
    top: 192px;
    height: 40px;
    background: var(--orange);
    color: #fff;
    font-size: 16px;
    font-weight: 400;
    display: flex;
    align-items: center;
    justify-content: center;
    gap: 8px;
    letter-spacing: 0.2px;
  }
  .services__sep { font-size: 12px; }
  .front-url {
    position: absolute;
    left: 0; right: 0;
    top: 248px;
    text-align: center;
    font-size: 15px;
    font-weight: 600;
    color: var(--ink);
    letter-spacing: 0.3px;
  }

  .person { position: absolute; left: 46px; top: 128px; }
  .person__name { font-size: 19px; font-weight: 600; color: var(--ink); }
  .person__title { font-size: 13px; color: var(--orange); margin-top: 4px; }

  .address {
    position: absolute;
    left: 20px; top: 196px;
    display: flex;
    gap: 8px;
    font-size: 12.5px;
    line-height: 1.4;
    color: var(--muted);
  }
  .icon { width: 13px; height: 13px; flex: none; margin-top: 2px; }

  .contacts {
    position: absolute;
    left: 282px; top: 172px;
    list-style: none;
    font-size: 12.5px;
    line-height: 1.45;
    color: var(--muted);
  }
  .contacts li { display: flex; align-items: center; gap: 8px; white-space: nowrap; }
  .contacts .icon { margin-top: 0; }
  .social-mark { width: 11px; height: 11px; background: var(--navy); border-radius: 2px; flex: none; margin: 0 1px; }
  .social-mark--round { border-radius: 50%; }
  .accent { color: var(--orange); }

  .back-band { position: absolute; left: 0; bottom: 0; width: 540px; height: 32px; }
</style>
</head>
<body>

  <section class="card card--front" aria-label="Business card front">
    <div class="brand">
      <span class="brand__dot"></span>
      <span class="brand__name">Trelvan Media</span>
    </div>
    <div class="services">
      <span>Web Design</span><span class="services__sep">•</span>
      <span>Internet Marketing</span><span class="services__sep">•</span>
      <span>Website Management</span>
    </div>
    <p class="front-url">www.trelvanmedia.example</p>
  </section>

  <section class="card card--back" aria-label="Business card back">
    <div class="brand">
      <span class="brand__dot"></span>
      <span class="brand__name">Trelvan Media</span>
    </div>

    <div class="person">
      <p class="person__name">Mark Lenner</p>
      <p class="person__title">President/CEO</p>
    </div>

    <div class="address">
      <svg class="icon" viewBox="0 0 16 16" aria-hidden="true"><path fill="#2b3f8f" d="M8 1 L1 7.5 H3 V15 H6.5 V10.5 H9.5 V15 H13 V7.5 H15 Z"/></svg>
      <p>4315 W. Calloway Ave. Ste. 140<br>Tucson, AZ 85792</p>
    </div>

    <ul class="contacts">
      <li>
        <svg class="icon" viewBox="0 0 16 16" aria-hidden="true"><rect x="1" y="3" width="14" height="10" rx="1.5" fill="#2b3f8f"/><path d="M1.5 4 L8 9 L14.5 4" stroke="#fff" stroke-width="1.3" fill="none"/></svg>
        <span>mark@trelvanmedia.example</span>
      </li>
      <li>
        <svg class="icon" viewBox="0 0 16 16" aria-hidden="true"><path fill="#2b3f8f" d="M4 1.5 L6.5 4.5 L5 6.5 C6 8.5 7.5 10 9.5 11 L11.5 9.5 L14.5 12 L12.5 14.5 C7 14 2 9 1.5 3.5 Z"/></svg>
        <span>520-381-7459</span>
      </li>
      <li>
        <svg class="icon" viewBox="0 0 16 16" aria-hidden="true"><path fill="#2b3f8f" d="M4 1.5 L6.5 4.5 L5 6.5 C6 8.5 7.5 10 9.5 11 L11.5 9.5 L14.5 12 L12.5 14.5 C7 14 2 9 1.5 3.5 Z"/></svg>
        <span>866-381-7459 (toll free)</span>
      </li>
      <li><span class="social-mark social-mark--round"></span><span>@trelvanmedia</span></li>
      <li><span class="social-mark"></span><span>www.<span class="accent">friendline.example</span>/trelvanmedia</span></li>
    </ul>

    <svg class="back-band" viewBox="0 0 540 32" preserveAspectRatio="none" aria-hidden="true">
      <path d="M0 14 L330 14 L318 32 L0 32 Z" fill="#2b3f8f"/>
      <path d="M0 8 L336 8 L330 14 L0 14 Z" fill="#1a86c7"/>
      <path d="M400 22 L540 22 L540 32 L392 32 Z" fill="#f07d1e"/>
    </svg>
  </section>

</body>
</html>
```